Custom unique Stationary design for Logistics company

We need a custom, unique , elegant and luxurious full stationary design using our new logo, following these guidelines:
1- Business card: double sided, both sides uses the navy blue as the background main color (same as the code of the navy blue used in our logo).
2- envelope and folder: also use the same navy blue as the main background color.
3- book cover( notepad cover) : same thing with the navy blue
4- letterhead: feel free to use the combination of the colors in our logo.
5- rest of the items are up to your creativity

Target Market(s)

corporates and other businesses

Industry/Entity Type

Logistics and heavy machines contractors

Requirements
Must have
• Letterhead, business card, envelope, notepad cover, paper, file
Nice to have
• navy blue to be main background color for business card, envelope, notepad cover

```html
<!DOCTYPE html>
<html lang="en">
<head>
<meta charset="utf-8">
<title>Business Card – Meridian Cargo Services</title>
<link rel="stylesheet" href="https://fonts.googleapis.com/css2?family=Exo+2:wght@300;400;500&display=swap">
<style>
  :root {
    --navy: #004f77;
    --navy-edge: #00456a;
    --orange: #f15f30;
    --white: #ffffff;
    --backdrop: #e4e6e8;
  }
  * { margin: 0; padding: 0; box-sizing: border-box; }
  html, body {
    width: 1200px; height: 1200px; overflow: hidden;
    background: var(--backdrop);
    font-family: "Exo 2", sans-serif;
  }
  .sheet { position: relative; width: 1200px; height: 1200px; }
  .card {
    position: absolute; left: 262px;
    width: 800px; height: 456px;
    transform: scale(0.857); transform-origin: top left;
    border-radius: 30px; overflow: hidden;
  }
  .card--front { top: 165px; background: var(--white); }
  .card--back { top: 653px; background: var(--navy); }
  .front-dome { position: absolute; inset: 0; width: 800px; height: 456px; }
  .holder { position: absolute; left: 51px; top: 306px; color: var(--white); }
  .holder__name { color: var(--orange); font-size: 28px; font-weight: 300; letter-spacing: 0.4px; line-height: 1; }
  .holder__title { font-size: 17px; font-weight: 400; margin-top: 8px; }
  .holder__address { font-size: 17px; font-weight: 400; line-height: 23px; margin-top: 9px; }
  .contacts {
    position: absolute; right: 50px; top: 319px;
    list-style: none; color: var(--white); font-size: 17px; font-weight: 400;
  }
  .contacts li { display: flex; align-items: center; justify-content: flex-end; height: 23px; }
  .contacts svg { width: 15px; height: 15px; margin-left: 10px; fill: var(--orange); flex: none; }
  .brand {
    position: absolute; left: 0; right: 0; top: 0; bottom: -12px;
    display: flex; align-items: center; justify-content: center; gap: 16px;
  }
  .brand__dot { width: 22px; height: 22px; border-radius: 50%; background: var(--orange); }
  .brand__name { color: var(--white); font-size: 34px; font-weight: 500; letter-spacing: 3px; }
</style>
</head>
<body>
<main class="sheet">
  <section class="card card--front">
    <svg class="front-dome" viewBox="0 0 800 456" aria-hidden="true">
      <path d="M0 252 A486 486 0 0 1 800 262 L800 456 L0 456 Z" fill="var(--navy)" stroke="var(--navy-edge)" stroke-width="3"/>
    </svg>
    <div class="holder">
      <h1 class="holder__name">DANIEL HARPER</h1>
      <p class="holder__title">President</p>
      <p class="holder__address">2914 Spruce Hollow Road<br>Anchorage, Alaska 99517</p>
    </div>
    <ul class="contacts">
      <li>907-555-0148
        <svg viewBox="0 0 16 16"><path d="M3 1l3 3-1.5 2a9 9 0 0 0 5.5 5.5l2-1.5 3 3-2 2C6 14 2 10 1 3z"/></svg></li>
      <li>907-555-0192
        <svg viewBox="0 0 16 16"><path d="M4 0h8a1 1 0 0 1 1 1v14a1 1 0 0 1-1 1H4a1 1 0 0 1-1-1V1a1 1 0 0 1 1-1zm1 2v10h6V2zm3 11a1 1 0 1 0 0 2 1 1 0 0 0 0-2z"/></svg></li>
      <li>info@meridiancargoservices.com
        <svg viewBox="0 0 16 16"><path d="M1 3h14v10H1zm1 1.5v.5l6 4 6-4v-.5z"/></svg></li>
      <li>meridiancargoservices.com
        <svg viewBox="0 0 16 16"><circle cx="8" cy="8" r="7"/><path d="M5 4c2 0 3 1 2 3s2 1 2 3-2 3-2 4M10 2c0 2 2 3 4 3" stroke="var(--navy)" stroke-width="1.3" fill="none"/></svg></li>
    </ul>
  </section>

  <section class="card card--back">
    <div class="brand">
      <span class="brand__dot"></span>
      <span class="brand__name">MERIDIAN CARGO SERVICES</span>
    </div>
  </section>
</main>
</body>
</html>
```